Stylist/Barber Standup Sign for Hair Regrowth Company

We want to design an attractive and eye-catching sign for hair stylists and barbers to sit on their workstations to attract the attention of their clients regarding hair loss and encourage them to speak to their stylist about it of they are would like to seek treatment.
50% of men and 25% of women suffer from hair loss but most are in denial that it is happening or too embarrassed to talk about it.

Copy for the flyer is as follows:

[Section 1:]
This flyer has been placed here/designed to spark conversation about hair loss

[Section 2:]
The truth is...
73% of people believe their hair is thinning
They are right

[Section 3:]
If you've got questions, your stylist or barber has answers.

Additional Background Information:

Primary target audience is men between the ages of 25-45, secondary target audience is men 46-60

Current Consumer Perception? (in the first person) “I’ve been thinking about my hair. I think it’s getting thinner and I’m scared, worried and don’t know what to do. But I don’t know if there is anything that really works. I’ve tried other things and nothing‘s worked.”

Tonality of materials? Very guy friendly, matter of fact, authoritative, its what you might hear from your best friend. Confident. Encouraging, but with a sense of urgency.

Please use our brand colors, but do not include our logo or brand name.
Colors are as follows:
Green: #4ca26f
Light Grey: #999999
Dark Grey: #262626

I have attached print templates in both PDF and Jpeg, please use those to provide final ready to print documents if you are selected.

Target Market(s)

Industry/Entity Type

Health And Wellness

Font styles to use
Sans Serif

Colors
00a990
ffffff
333333
cbcbcb

Requirements
Must have
• We want to get across the following messaging. Ideally you will submit a design using our copy and if you think you can do better, please feel free to submit another design with your own copy/messaging. If you can do it better we would love to select you :-)
• Our copy?
• This flyer has been placed here/designed to spark conversation about hair loss
• The truth is...
• 73% of people believe their hair is thinning
• They are right
• If you've got questions, your stylist or barber has answers
• Also please use our brand colors:
• Green: #4ca26f
• Light Grey: #999999
• Dark Grey: #262626
Should not have
• dont add any logos, images or ornate design. this needs to be simple, easy to ready and eye catching.
• do not use the color red in any capacity.

```html
<!DOCTYPE html>
<html lang="en">
<head>
<meta charset="utf-8">
<title>Worried about hair loss? – Workstation Sign</title>
<link rel="stylesheet" href="https://fonts.googleapis.com/css2?family=Andika&display=swap">
<style>
  :root {
    --bg-dark: #363636;
    --accent-teal: #3fae96;
    --text-light: #ffffff;
    --text-dark: #2e2e2e;
  }
  * { margin: 0; padding: 0; box-sizing: border-box; }
  html, body {
    width: 806px;
    height: 1200px;
    overflow: hidden;
    background: var(--bg-dark);
  }
  .sign {
    position: relative;
    width: 806px;
    height: 1200px;
    background: var(--bg-dark);
    font-family: "Andika", "Trebuchet MS", sans-serif;
    color: var(--text-light);
    overflow: hidden;
  }
  .edge-line {
    position: absolute;
    left: 0;
    top: 0;
    width: 3px;
    height: 520px;
    background: var(--accent-teal);
    opacity: 0.6;
  }
  .headline {
    position: absolute;
    top: 22px;
    left: 72px;
    width: 666px;
    text-align: center;
    font-size: 50px;
    font-weight: 400;
    line-height: 1.15;
    padding-bottom: 4px;
    border-bottom: 3px solid var(--accent-teal);
  }
  .subhead {
    position: absolute;
    top: 94px;
    left: 0;
    width: 806px;
    text-align: center;
    font-size: 42px;
    font-weight: 400;
    line-height: 1.2;
  }
  .fact-panel {
    position: absolute;
    left: 100px;
    top: 240px;
    width: 600px;
    height: 300px;
  }
  .fact-panel svg {
    position: absolute;
    inset: 0;
    width: 100%;
    height: 100%;
  }
  .fact-panel svg polygon { fill: var(--accent-teal); }
  .fact-text {
    position: absolute;
    inset: 0;
    display: flex;
    flex-direction: column;
    justify-content: center;
    align-items: center;
    text-align: center;
    color: var(--text-dark);
    font-size: 45px;
    line-height: 66px;
    padding-top: 4px;
  }
  .closing {
    position: absolute;
    top: 836px;
    left: 0;
    width: 806px;
    text-align: center;
    font-size: 41px;
    line-height: 56.5px;
  }
</style>
</head>
<body>
  <main class="sign">
    <div class="edge-line"></div>

    <h1 class="headline">Worried about hair loss?</h1>
    <p class="subhead">Does your hair seem thinner?</p>

    <section class="fact-panel">
      <svg viewBox="0 0 600 300" preserveAspectRatio="none" aria-hidden="true">
        <polygon points="12,14 30,4 42,14 60,8 75,14 95,2 110,14 130,9 150,14 170,3 185,14 210,7 230,14 255,1 270,14 300,9 320,14 340,4 355,14 380,8 400,14 420,2 440,14 465,7 485,14 505,3 520,14 545,9 560,14 580,4 588,16 582,35 596,55 583,75 594,100 582,125 598,150 583,175 592,200 582,225 597,250 582,272 590,290 565,284 550,296 530,285 510,298 490,286 465,294 445,285 420,299 400,286 375,293 355,285 330,298 310,286 285,295 265,285 240,299 220,286 195,293 175,285 150,298 130,286 105,294 85,285 60,299 40,286 20,296 10,284 0,265 12,245 2,220 13,195 4,170 12,145 1,120 13,95 3,70 12,45 2,25"/>
      </svg>
      <p class="fact-text">
        <span>Did you know that 73%</span>
        <span>of people have these fears.</span>
      </p>
    </section>

    <p class="closing">
      Hair loss can occur at any age,<br>
      it can be difficult to talk about<br>
      but if you have any concerns<br>
      about your hair, speak to your<br>
      barber or stylist today.
    </p>
  </main>
</body>
</html>
```